Employee Benefits and Insurance Consulting

We are an existing company with over 30 years experience but are changing our name. We would like a simple design with grey tones.

Industry/Entity Type

Insurance

Contact Information for Business Card

Marlow Benefits Consulting
Gerald P Hollins CEO
5172 Brackenridge Road
Cedar Hollow, TN 37802
gerald@marlowbenefits-example.com
865-412-5593 - O
865-247-3861 - C

```html
<!DOCTYPE html>
<html lang="en">
<head>
<meta charset="utf-8">
<title>Marlow Benefits Consulting – Business Card</title>
<link rel="stylesheet" href="https://fonts.googleapis.com/css2?family=Open+Sans:wght@400;600&display=swap">
<style>
  :root {
    --teal: #1f9688;
    --grey: #666666;
    --ink: #2b2b2b;
    --card: #ffffff;
    --backdrop: #e9e9e9;
  }
  * { box-sizing: border-box; margin: 0; padding: 0; }
  html, body {
    width: 1200px; height: 900px; overflow: hidden;
    background: var(--backdrop);
    font-family: "Open Sans", Arial, sans-serif;
  }
  .canvas { position: relative; width: 1200px; height: 900px; }

  .card {
    position: absolute;
    background: var(--card);
    border-radius: 14px;
    overflow: hidden;
    box-shadow: 0 4px 14px rgba(0,0,0,0.12);
  }
  .card--front { left: 78px; top: 35px; width: 588px; height: 362px; }
  .card--back  { left: 389px; top: 506px; width: 565px; height: 350px; }

  .bar { position: absolute; background: var(--teal); }

  .brand {
    position: absolute;
    text-align: center;
    color: var(--teal);
    font-weight: 600;
    text-transform: uppercase;
    letter-spacing: 1px;
    line-height: 1.15;
  }
  .brand__mark {
    display: block;
    margin: 0 auto 12px;
    background: var(--grey);
  }
  .card--front .brand { left: 290px; top: 30px; width: 260px; font-size: 22px; }
  .card--front .brand__mark { width: 44px; height: 44px; }
  .card--back .brand { left: 133px; top: 100px; width: 300px; font-size: 25px; }
  .card--back .brand__mark { width: 50px; height: 50px; }

  .person {
    position: absolute; left: 29px; top: 229px;
    color: var(--teal); font-size: 20px; font-weight: 600;
  }
  .person__role { font-size: 15px; }

  .contacts {
    position: absolute; left: 29px; top: 268px;
    list-style: none; color: var(--ink); font-size: 14px;
  }
  .contacts li { display: flex; align-items: center; height: 24.5px; white-space: nowrap; }
  .contacts svg { width: 12px; height: 12px; margin-right: 12px; fill: var(--teal); flex: none; }

  .address {
    position: absolute; right: 90px; top: 296px;
    text-align: right; color: var(--ink); font-size: 14px; line-height: 21px;
    font-style: normal; white-space: nowrap;
  }
</style>
</head>
<body>
<main class="canvas">

  <section class="card card--front" aria-label="Business card front">
    <span class="bar" style="left:29px;top:0;width:9px;height:219px"></span>
    <span class="bar" style="left:44px;top:0;width:8px;height:219px"></span>

    <div class="brand">
      <span class="brand__mark"></span>
      Marlow Benefits<br>Consulting
    </div>

    <p class="person">Gerald P Hollins <span class="person__role">- CEO</span></p>

    <ul class="contacts">
      <li>
        <svg viewBox="0 0 24 24" aria-hidden="true"><path d="M6.6 10.8a15.1 15.1 0 0 0 6.6 6.6l2.2-2.2a1 1 0 0 1 1-.25 11.4 11.4 0 0 0 3.6.57 1 1 0 0 1 1 1V20a1 1 0 0 1-1 1A17 17 0 0 1 3 4a1 1 0 0 1 1-1h3.5a1 1 0 0 1 1 1c0 1.25.2 2.45.57 3.6a1 1 0 0 1-.25 1z"/></svg>
        865-247-3861
      </li>
      <li>
        <svg viewBox="0 0 24 24" aria-hidden="true"><path d="M7 1h10a2 2 0 0 1 2 2v18a2 2 0 0 1-2 2H7a2 2 0 0 1-2-2V3a2 2 0 0 1 2-2zm0 3v14h10V4zm5 15.5a1.2 1.2 0 1 0 0 2.4 1.2 1.2 0 0 0 0-2.4z"/></svg>
        865-412-5593
      </li>
      <li>
        <svg viewBox="0 0 24 24" aria-hidden="true"><path d="M2 5h20v14H2zm2 2v.5l8 5 8-5V7l-8 5z"/></svg>
        gerald@marlowbenefits-example.com
      </li>
    </ul>

    <address class="address">5172 Brackenridge Road<br>Cedar Hollow, TN 37802</address>

    <span class="bar" style="left:519px;top:310px;width:69px;height:10px"></span>
    <span class="bar" style="left:519px;top:326px;width:69px;height:9px"></span>
  </section>

  <section class="card card--back" aria-label="Business card back">
    <div class="brand">
      <span class="brand__mark"></span>
      Marlow Benefits<br>Consulting
    </div>
    <span class="bar" style="left:507px;top:0;width:8px;height:350px"></span>
    <span class="bar" style="left:521px;top:0;width:8px;height:350px"></span>
  </section>

</main>
</body>
</html>
```